Sable Grove products by Voldrin. Beauty, skin care cosmetic products

We are an all natural and organic beauty product company looking for a logo an label design ideas. Our motto is to make products that are safe, natural, in harmony with the earth and that really work. Our products will contribute to the transition from the Old Earth to the Sable Grove (as the image of the two worlds suggests). The earths can be mixed in the label. The label example is a rough sketch.
Updates

The label needs to be 1 (one) inch high and 7 inch long.

Need extra days to review

Target Market(s)

Products made with natural and organic ingredients. Beauty and skin products

Requirements
Must have
• My project must be standing out. We want customers to be draw to he product on the shelf. Wow, this label is different? what is it? All natural? I must try it.
• Must be bold but not outrageous.
• The two earth can be placed on right and left side of the tree of life on the second attachment
Nice to have
• The two Earth can be in the back ground suggesting that this product takes us from chemically and artificially filled products to something new that is in harmony with nature and health.
Should not have
• Should not be boring. Ordinary, easy to forget and ignore patterns, lettering, logos.

```html
<!DOCTYPE html>
<html lang="en">
<head>
<meta charset="utf-8">
<title>Sable Grove Products by Voldrin – Under-Arm-Balm Label</title>
<link href="https://fonts.googleapis.com/css2?family=Alegreya:wght@400;500&family=Fira+Sans+Condensed:wght@300;400;700&family=Oswald:wght@600&display=swap" rel="stylesheet">
<style>
  :root {
    --page: #e7e8ea;
    --blue: #1f63bd;
    --blue-deep: #123f8a;
    --night: #07091a;
    --green: #7dc242;
    --white: #ffffff;
    --ink: #1b1b1b;
  }
  * { box-sizing: border-box; margin: 0; padding: 0; }
  html, body { width: 1200px; height: 783px; overflow: hidden; }
  body { background: var(--page); position: relative; font-family: "Alegreya", Georgia, serif; }

  .label {
    position: absolute; left: 40px; top: 311px; width: 1120px; height: 160px;
    background: linear-gradient(90deg, var(--blue) 0%, var(--blue-deep) 30%, var(--night) 45%, var(--night) 62%, var(--blue-deep) 72%, var(--blue) 100%);
    color: var(--white); overflow: hidden;
    box-shadow: 0 8px 18px rgba(0,0,0,.35);
  }
  .label > * { position: absolute; line-height: 1; }
  .label__world { top: -40px; width: 300px; height: 240px; border-radius: 50%; }
  .label__world--old { left: 140px; background: radial-gradient(circle, rgba(20,40,60,.55), rgba(20,40,60,0) 70%); }
  .label__world--new { left: 700px; background: radial-gradient(circle, rgba(60,120,220,.55), rgba(60,120,220,0) 70%); }
  .label__tree {
    left: 395px; top: -10px; width: 340px; height: 180px; border-radius: 50%;
    background: radial-gradient(ellipse, rgba(35,80,70,.35) 0%, rgba(10,20,40,.2) 55%, rgba(0,0,0,0) 72%);
  }

  .panel-info { left: 24px; top: 14px; width: 284px; font-size: 10.6px; }
  .panel-info p { line-height: 12.2px; }
  .panel-info p + p { margin-top: 5px; }
  .tag { font-family: "Fira Sans Condensed", sans-serif; font-weight: 700; font-size: 10.4px; }
  .warning { left: 16px; top: 114px; width: 303px; height: 35px; border: 1px solid var(--white); padding: 4px 7px; font-size: 10.6px; line-height: 12.6px !important; }

  .scent {
    left: 362px; top: 80px; transform: translate(-50%, -50%) rotate(-90deg);
    color: var(--green); font-size: 19px; white-space: nowrap; letter-spacing: .3px;
  }

  .brand { left: 400px; width: 320px; text-align: center; white-space: nowrap; }
  .brand__name { top: 19px; font-size: 20.5px; letter-spacing: .5px; }
  .brand__by { top: 40px; font-size: 16px; }
  .brand__by b { font-family: "Fira Sans Condensed", sans-serif; font-weight: 700; font-size: 22px; }
  .product { top: 73px; font-family: "Oswald", sans-serif; font-weight: 600; font-size: 26px; color: var(--green); letter-spacing: 1px; }
  .claim { top: 112px; font-size: 13px; letter-spacing: .4px; }
  .free { top: 129px; font-family: "Fira Sans Condensed", sans-serif; font-weight: 300; font-size: 13.2px; }
  .free b { font-weight: 700; }

  .maker { left: 799px; top: 26px; font-size: 11.8px; line-height: 14px !important; }
  .learn { left: 799px; top: 66px; font-size: 11.8px; }
  .learn span { font-size: 15px; }
  .best { left: 799px; top: 94px; width: 128px; height: 16px; background: var(--white); color: var(--ink); font-size: 10.5px; padding: 3px 6px; }
  .weight { left: 801px; top: 122px; font-size: 12px; }

  .mark { left: 988px; display: block; }
  .mark--recycle { top: 14px; }
  .mark--cruelty { top: 66px; }
  .mark--social { top: 109px; }
</style>
</head>
<body>
  <section class="label">
    <div class="label__world label__world--old" role="img" aria-label="Old Earth globe in the background"></div>
    <div class="label__world label__world--new" role="img" aria-label="Renewed, greener globe in the background"></div>
    <div class="label__tree" role="img" aria-label="Tree of life ornament with knotwork border"></div>

    <div class="panel-info">
      <p><span class="tag">INGREDIENTS:</span> Organic Coconut (Cocos nucifera) Oil, Organic Bees Wax,Shea (Butyrospermum Parkii) Butter, Arrowroot (Mainhot Esculenta) Powder, Magnesium Oil, Nahcolite (Natural Baking Soda)</p>
      <p><span class="tag">DIRECTIONS:</span> With the finger or spatula apply a pee size product under the arm and spred it on, if applied night after a shave it might sting a bit. Wait a few minutes and the apply.</p>
    </div>
    <div class="warning"><span class="tag">WARNING:</span> External use only. Discontinue use if irritation occurs. Do not apply to open cuts or wounds.</div>

    <div class="scent">Orignal Scent</div>

    <div class="brand brand__name">Sable Grove Products</div>
    <div class="brand brand__by">by <b>VOLDRIN</b></div>
    <div class="brand product">UNDER-ARM-BALM</div>
    <div class="brand claim">100% NATURAL INGREDIENTS</div>
    <div class="brand free"><b>No</b> Aluminum, <b>No</b> Parabens, <b>No</b> Phthalates</div>

    <div class="maker">Manufactured by Voldrin LLC<br>Fenwick Ridge MD 20417</div>
    <div class="learn">Lear more at: <span>VOLDRIN.COM</span></div>
    <div class="best">Best before: 11-21-11</div>
    <div class="weight">Net Wt. 2oz (56 g)</div>

    <svg class="mark mark--recycle" width="40" height="40" viewBox="0 0 40 40" role="img" aria-label="Recycling badge"><polygon points="20,4 36,34 4,34" fill="none" stroke="var(--green)" stroke-width="3"/></svg>
    <svg class="mark mark--cruelty" width="40" height="36" viewBox="0 0 40 36" role="img" aria-label="Cruelty-free badge"><circle cx="20" cy="18" r="15" fill="none" stroke="var(--white)" stroke-width="2"/></svg>
    <svg class="mark mark--social" width="40" height="40" viewBox="0 0 40 40" role="img" aria-label="Social channels">
      <circle cx="10" cy="10" r="8" fill="var(--white)"/><circle cx="30" cy="10" r="8" fill="var(--white)"/>
      <circle cx="10" cy="30" r="8" fill="var(--white)"/><circle cx="30" cy="30" r="8" fill="var(--white)"/>
    </svg>
  </section>
</body>
</html>
```